Local Flower Farm Needs Business Card Design

I need business cards designed for a flower farm based in Eudora, Kansas.
Business Info:
We are a local cut flower farm located in Eudora, Kansas, founded by Corinne Haldwick. What started as a passion for agriculture and search for more joy in daily life has blossomed into a small business dedicated to providing the community with beautiful, fresh, and sustainable flowers. We specialize in local, seasonal blooms, ensuring that every petal reflects the care and dedication we pour into our craft. Our mission is to deliver the highest quality flowers directly to our customers through local farmers markets and to florists who share our commitment to sustainability. Join us in celebrating the beauty of nature, one bloom at a time!
Contact Details:
Corinne Haldwick
Owner
Phone 913-555-0147
Facebook: Rosalind Thorpe Gardens
Instagram: @RosalindThorpeGardens
Website: RosalindThorpeGardens.example
Target Market(s)
Wholesale to Florists and Direct to Consumer via Farmers Market
Industry/Entity Type
Florist, Farm
Contact Information for Business Card
Name, Contact Info, Logo
Look and feel
Each slider illustrates characteristics of the customer's brand and the style your logo design should communicate.

```html
<!DOCTYPE html>
<html lang="en">
<head>
<meta charset="utf-8">
<title>Rosalind Thorpe Gardens — Business Card</title>
<link rel="stylesheet" href="https://fonts.googleapis.com/css2?family=Arimo:wght@400;700&display=swap">
<style>
  :root {
    --backdrop: #2a2c2f;
    --card-top: #0e363c;
    --card-bottom: #09252a;
    --ink: #ffffff;
    --ink-soft: #c9d3d4;
    --ink-faint: rgba(255,255,255,0.06);
    --bar: #ffffff;
  }
  * { box-sizing: border-box; margin: 0; padding: 0; }
  html, body {
    width: 1200px; height: 900px; overflow: hidden;
    background: var(--backdrop);
    font-family: "Arimo", Arial, sans-serif;
  }
  .sheet {
    position: relative; width: 1200px; height: 900px;
    display: flex; align-items: center; justify-content: center; gap: 40px;
  }
  .card {
    position: relative; width: 540px; height: 309px;
    background: linear-gradient(160deg, var(--card-top), var(--card-bottom));
    border-radius: 4px; overflow: hidden;
    box-shadow: 0 18px 40px rgba(0,0,0,0.45);
  }
  /* Front: contact side */
  .brand-mark {
    position: absolute; left: 34px; top: 26px;
    width: 96px; height: 96px; border-radius: 50%;
    border: 1.5px solid var(--ink);
    display: flex; align-items: center; justify-content: center; text-align: center;
    color: var(--ink); font-size: 11px; font-weight: 400; letter-spacing: 1.5px;
    text-transform: uppercase; line-height: 1.4; padding: 10px;
  }
  .person { position: absolute; left: 34px; top: 136px; color: var(--ink); }
  .person-name { font-size: 19px; font-weight: 700; letter-spacing: 0.5px; text-transform: uppercase; }
  .person-role { font-size: 11px; color: var(--ink-soft); margin-top: 3px; }
  .person-rule { width: 8px; height: 1px; background: var(--ink-soft); margin: 8px 0 10px; }
  .contact-list { list-style: none; font-size: 13px; color: var(--ink); }
  .contact-list li { display: flex; align-items: center; gap: 7px; margin-bottom: 5px; }
  .contact-list svg { width: 10px; height: 10px; flex: none; }
  .decor-wash {
    position: absolute; right: 60px; top: 40px; width: 210px; height: 210px;
    border-radius: 50%; background: var(--ink-faint);
  }
  .website {
    position: absolute; right: 30px; bottom: 44px;
    color: var(--ink); font-size: 15px; letter-spacing: 0.2px;
  }
  .accent-bar {
    position: absolute; right: 0; bottom: 0; width: 280px; height: 26px; background: var(--bar);
  }
  /* Back: brand side */
  .card-back { display: flex; align-items: center; justify-content: center; }
  .brand-seal {
    width: 150px; height: 150px; border-radius: 50%;
    border: 1.5px solid var(--ink);
    display: flex; align-items: center; justify-content: center; text-align: center;
    color: var(--ink); font-size: 15px; letter-spacing: 2px; text-transform: uppercase;
    line-height: 1.5; padding: 16px;
  }
</style>
</head>
<body>
<main class="sheet">
  <section class="card card-front">
    <div class="decor-wash" aria-hidden="true"></div>
    <div class="brand-mark">Rosalind Thorpe Gardens</div>
    <div class="person">
      <h1 class="person-name">Corinne Haldwick</h1>
      <p class="person-role">Owner</p>
      <div class="person-rule"></div>
      <ul class="contact-list">
        <li>
          <svg viewBox="0 0 10 10" aria-hidden="true"><path d="M2 0.8 L3.6 2.8 L2.8 4 Q4 6.2 6 7.2 L7.2 6.4 L9.2 8 L8.2 9.4 Q3.8 9 0.6 1.8 Z" fill="#fff"/></svg>
          913-555-0147
        </li>
        <li>
          <svg viewBox="0 0 10 10" aria-hidden="true"><circle cx="5" cy="5" r="4.5" fill="#fff"/></svg>
          Rosalind Thorpe Gardens
        </li>
        <li>
          <svg viewBox="0 0 10 10" aria-hidden="true"><circle cx="5" cy="5" r="4.5" fill="none" stroke="#fff" stroke-width="1.2"/></svg>
          @RosalindThorpeGardens
        </li>
      </ul>
    </div>
    <p class="website">RosalindThorpeGardens.example</p>
    <div class="accent-bar"></div>
  </section>

  <section class="card card-back">
    <div class="brand-seal">Rosalind Thorpe Gardens</div>
  </section>
</main>
</body>
</html>
```